Business Card Design Project

We are not a new company, but renamed to "Vantorin Kitchens" last year. We specialize in modern high-end cabinetry imports. We would like to communicate a sense of quality and cutting edge technology. Ideally the design would incorporate our logo colors, silver, red and preferably a black, matte background. Though we are open to suggestions.
Logo is attached.
Edit: I have attached rough drafts of the previous cards, this way you will have all necessary content that needs to go on the cards.
Updates
Project Deadline Extended
Reason: We have received a lot of great designs, but due to the sheer number we couldn't respond to all. We will extend the deadline for another 7 days to finalize and provide feedback to designers.
Thank you for your hard work!
Industry/Entity Type
Business
Look and feel
Each slider illustrates characteristics of the customer's brand and the style your logo design should communicate.

```html
<!DOCTYPE html>
<html lang="en">
<head>
<meta charset="utf-8">
<title>Vantorin Kitchens — Business Cards</title>
<link href="https://fonts.googleapis.com/css2?family=Arimo:wght@400;700&display=swap" rel="stylesheet">
<style>
  :root{
    --stage:#d9d6d2;
    --card-black:#141414;
    --card-dark:#262626;
    --silver-light:#e4e4e4;
    --silver-mid:#b8b8b8;
    --silver-dark:#7a7a7a;
    --red:#e0141c;
    --ink-light:#ffffff;
    --ink-dark:#1a1a1a;
    --label:#1f1f1f;
  }
  *{box-sizing:border-box;margin:0;padding:0}
  html,body{width:1200px;height:788px;overflow:hidden}
  body{background:var(--stage);font-family:"Arimo",Arial,sans-serif;position:relative}
  .label{position:absolute;width:527px;text-align:center;font-size:20px;color:var(--label)}
  .card{position:absolute;width:527px;height:300px;border-radius:20px;overflow:hidden;
    background:radial-gradient(ellipse at 40% 30%,var(--card-dark),var(--card-black) 75%);
    box-shadow:0 2px 6px rgba(0,0,0,.35)}
  .card svg.wave{position:absolute;inset:0}
  .brand{position:absolute;display:flex;flex-direction:column;align-items:center;gap:14px}
  .brand-mark{width:42px;height:42px;background:var(--silver-mid)}
  .brand-name{font-weight:700;color:var(--silver-mid);letter-spacing:2px;white-space:nowrap}
  .front .brand{left:30px;top:24px}
  .front .brand-name{font-size:24px}
  .person{position:absolute;left:30px;top:150px;color:var(--ink-light)}
  .person-name{font-size:16px;font-weight:700}
  .person-name span{font-weight:400;font-size:15px}
  .person-phones{margin-top:10px;font-size:13px;line-height:22px}
  .person-phones b{font-weight:700}
  .office{position:absolute;right:30px;top:212px;text-align:right;color:var(--ink-dark);font-size:13px;line-height:26px}
  .back .brand{left:0;right:0;top:90px}
  .back .brand-name{font-size:26px}
  .dots{position:absolute;border-radius:50%}
</style>
</head>
<body>
  <div class="label" style="left:53px;top:24px">front</div>
  <div class="label" style="left:624px;top:24px">front-1</div>
  <div class="label" style="left:56px;top:406px">back</div>
  <div class="label" style="left:624px;top:406px">Back - 1</div>

  <!-- Front: President -->
  <section class="card front" style="left:53px;top:74px">
    <svg class="wave" width="527" height="300" viewBox="0 0 527 300" aria-hidden="true">
      <defs>
        <linearGradient id="silverA" x1="0" y1="0" x2="1" y2="1">
          <stop offset="0" stop-color="#eeeeee"/><stop offset="1" stop-color="#b4b4b4"/>
        </linearGradient>
      </defs>
      <path d="M0,236 C140,262 240,240 320,175 C400,115 460,100 527,96 L527,106 C460,110 400,130 330,185 C250,250 150,275 0,250Z" fill="#8a8a8a"/>
      <path d="M0,238 C120,275 200,262 250,248 C170,276 90,276 0,262Z" fill="var(--red)"/>
      <path d="M0,262 C90,282 180,276 250,252 C320,226 380,150 527,108 L527,300 L0,300Z" fill="#0c0c0c"/>
      <path d="M0,270 C110,295 220,280 290,225 C370,160 440,118 527,110 L527,300 L0,300Z" fill="url(#silverA)"/>
    </svg>
    <div class="brand"><div class="brand-mark"></div><div class="brand-name">VANTORIN KITCHENS</div></div>
    <div class="person">
      <div class="person-name">MAREK DALTON, <span>President</span></div>
      <div class="person-phones"><b>phone</b> : 555.210.0599<br><b>cell</b> : 555.318.4426</div>
    </div>
    <div class="office"><b>fax</b> : 555.210.0519<br>marek@vantorinkitchens.ca<br>4120 - 87 Ave., Northfield, AB T5X 2K4</div>
  </section>

  <!-- Front: Director -->
  <section class="card front" style="left:624px;top:74px">
    <svg class="wave" width="527" height="300" viewBox="0 0 527 300" aria-hidden="true">
      <defs>
        <linearGradient id="silverB" x1="0" y1="0" x2="1" y2="1">
          <stop offset="0" stop-color="#eeeeee"/><stop offset="1" stop-color="#b4b4b4"/>
        </linearGradient>
      </defs>
      <path d="M0,236 C140,262 240,240 320,175 C400,115 460,100 527,96 L527,106 C460,110 400,130 330,185 C250,250 150,275 0,250Z" fill="#8a8a8a"/>
      <path d="M0,238 C120,275 200,262 250,248 C170,276 90,276 0,262Z" fill="var(--red)"/>
      <path d="M0,262 C90,282 180,276 250,252 C320,226 380,150 527,108 L527,300 L0,300Z" fill="#0c0c0c"/>
      <path d="M0,270 C110,295 220,280 290,225 C370,160 440,118 527,110 L527,300 L0,300Z" fill="url(#silverB)"/>
    </svg>
    <div class="brand"><div class="brand-mark"></div><div class="brand-name">VANTORIN KITCHENS</div></div>
    <div class="person">
      <div class="person-name" style="font-weight:400">OSKAR DALTON, <span style="font-size:13px">Director</span></div>
      <div class="person-phones"><b>phone</b> : 555.210.0599<br><b>cell</b> : 555.647.2093</div>
    </div>
    <div class="office"><b>fax</b> : 555.210.0519<br>oskar@vantorinkitchens.ca<br>4120 - 87 Ave., Northfield, AB T5X 2K4</div>
  </section>

  <!-- Back -->
  <section class="card back" style="left:56px;top:446px">
    <div class="brand"><div class="brand-mark"></div><div class="brand-name">VANTORIN KITCHENS</div></div>
  </section>

  <!-- Back - 1 -->
  <section class="card back" style="left:624px;top:446px;background:#050505">
    <div class="dots" role="img" aria-label="Perforated metal texture" style="left:-20px;top:-60px;width:260px;height:140px;background:radial-gradient(ellipse,#3c3c3c,rgba(5,5,5,0) 70%)"></div>
    <div class="dots" role="img" aria-label="Perforated metal texture" style="left:280px;top:200px;width:280px;height:140px;background:radial-gradient(ellipse,#3c3c3c,rgba(5,5,5,0) 70%)"></div>
    <div class="brand"><div class="brand-mark"></div><div class="brand-name">VANTORIN KITCHENS</div></div>
  </section>
</body>
</html>
```